Fresh, modern, fun business card for pediatric dental practice

Need a business card for fresh, modern, fun pediatric dental practice

Clean look that matches our website's font and colors

We prefer the look of curved corners on business cards

Target Market(s)

parents (mothers) of young children, professionals, mid-high class

Industry/Entity Type

Dental

Contact Information for Business Card

Maplebrook Pediatric Dentistry
482 Quarry Lane
Suite 517
Fernwood, PA 17599
717.555.0193
www.maplebrookkidsdental.example

Mei-Ran Tsai, DMD
Corinne Walbeck, DMD
(we are working on our email address, but we would like that on the card as well)

Font styles to use
Sans Serif

Requirements
Must have
• All info; we would also like to make cards for individual staff members
• colors from our website and color palatte, attatched
• use same font and design as website for branding
Nice to have
• clean, simple card that has a pop of color
• we would like to see a few designs with our tag line "where smiles get brighter"
• we are not sure if we want to have it on there or not
• we would like to see a few designs incorporating the ribbon graphic on our website where the word WELCOME is

```html
<!DOCTYPE html>
<html lang="en">
<head>
<meta charset="utf-8">
<title>Maplebrook Pediatric Dentistry – Business Card</title>
<link rel="stylesheet" href="https://fonts.googleapis.com/css2?family=Open+Sans:wght@300;400;700&family=Poppins:wght@500&family=Questrial&display=swap">
<style>
  :root {
    --backdrop: #262626;
    --plum: #512a50;
    --sun: #fdb927;
    --berry: #d6379a;
    --ink: #ffffff;
  }
  * { box-sizing: border-box; margin: 0; padding: 0; }
  html, body { width: 1200px; height: 897px; overflow: hidden; background: var(--backdrop); }
  .canvas { position: relative; width: 1200px; height: 897px; }
  .card {
    position: absolute; left: 353px; width: 486px; height: 277px;
    background: var(--plum); overflow: hidden;
  }
  .card--front { top: 162px; }
  .card--back { top: 468px; }

  .wordmark {
    font-family: "Open Sans", sans-serif; font-weight: 700; color: var(--sun);
    letter-spacing: 2px; line-height: 1;
  }
  .tagline {
    font-family: "Open Sans", sans-serif; font-weight: 300; color: var(--berry);
    letter-spacing: 2.2px; line-height: 1;
  }
  .card--front .brand { position: absolute; left: 0; right: 0; top: 112px; text-align: center; }
  .card--front .wordmark { font-size: 46px; }
  .card--front .tagline { font-size: 24px; margin-top: 8px; }

  .card--back .brand { position: absolute; left: 18px; top: 14px; z-index: 1; }
  .card--back .wordmark { font-size: 37px; }
  .card--back .tagline { font-size: 20px; margin-top: 4px; letter-spacing: 1.6px; }

  .doctor {
    position: absolute; left: 19px; top: 92px; z-index: 1;
    font-family: "Poppins", sans-serif; font-weight: 500; font-size: 18px; color: var(--ink);
  }
  .contacts { position: absolute; left: 22px; top: 127px; list-style: none; z-index: 1; }
  .contacts li {
    display: flex; align-items: center; gap: 8px; height: 19px;
    font-family: "Questrial", sans-serif; font-size: 13.5px; color: var(--ink);
    white-space: nowrap;
  }
  .contacts svg { width: 13px; height: 13px; flex: none; }
  .practice { position: absolute; left: 26px; top: 198px; z-index: 1; }
  .practice-title {
    font-family: "Open Sans", sans-serif; font-weight: 700; font-size: 10.5px;
    letter-spacing: 0.9px; color: var(--sun); margin-bottom: 4px;
  }
  .practice address {
    font-style: normal; font-family: "Questrial", sans-serif; font-size: 12px;
    line-height: 15px; color: var(--ink);
  }
  .brand-decoration {
    position: absolute; right: 0; top: 0; width: 200px; height: 277px;
    background: radial-gradient(circle at 58% 50%, rgba(253,185,39,0.55) 0%, rgba(253,185,39,0.18) 42%, rgba(81,42,80,0) 68%);
  }
</style>
</head>
<body>
<main class="canvas">
  <section class="card card--front" aria-label="Card front">
    <div class="brand">
      <div class="wordmark">maplebrook</div>
      <div class="tagline">pediatric dentistry</div>
    </div>
  </section>

  <section class="card card--back" aria-label="Card back">
    <div class="brand-decoration" role="img" aria-label="Large brand mark decoration in warm yellow"></div>
    <div class="brand">
      <div class="wordmark">maplebrook</div>
      <div class="tagline">pediatric dentistry</div>
    </div>
    <h1 class="doctor">Mei-Ran Tsai, DMD</h1>
    <ul class="contacts">
      <li>
        <svg viewBox="0 0 14 14" aria-hidden="true"><circle cx="7" cy="7" r="6.2" fill="none" stroke="#fdb927" stroke-width="1"/><path d="M5 3.8l1.2 1.6-.8.9c.5 1 1.3 1.8 2.3 2.3l.9-.8 1.6 1.2-.7 1.2C7 10.2 3.8 7 3.8 4.5z" fill="#fdb927"/></svg>
        717.555.0193
      </li>
      <li>
        <svg viewBox="0 0 14 14" aria-hidden="true"><circle cx="7" cy="7" r="6.2" fill="none" stroke="#fdb927" stroke-width="1"/><rect x="4" y="4.8" width="6" height="4.4" fill="none" stroke="#fdb927" stroke-width="0.9"/><path d="M4 4.8l3 2.4 3-2.4" fill="none" stroke="#fdb927" stroke-width="0.9"/></svg>
        info@maplebrookkidsdental.example
      </li>
      <li>
        <svg viewBox="0 0 14 14" aria-hidden="true"><circle cx="7" cy="7" r="6.2" fill="none" stroke="#fdb927" stroke-width="1"/><circle cx="7" cy="7" r="3.3" fill="none" stroke="#fdb927" stroke-width="0.8"/><path d="M3.7 7h6.6M7 3.7v6.6" stroke="#fdb927" stroke-width="0.8"/></svg>
        www.maplebrookkidsdental.example
      </li>
    </ul>
    <div class="practice">
      <div class="practice-title">MAPLEBROOK PEDIATRIC DENTISTRY</div>
      <address>Maplebrook Pediatric Dentistry<br>482 Quarry Lane<br>Suite 517, Fernwood, PA 17599</address>
    </div>
  </section>
</main>
</body>
</html>
```